KBT Business Cards

We require business cards for our business. We would like a matte black back to the card, with our logo centred in the middle. The front side of the card is open to design.

Target Market(s)

Clients looking for legal services (professional)

Industry/Entity Type

Legal

Contact Information for Business Card

Doran Kelbrath
Partner
Mobile: 0461 738 524
Email: doran@kbtlaw.co
Website: www.kbtlaw.co
Level 3, 118 Wendmore Street
Sydney NSW 2000

Font styles to use
Other font styles liked:
• Avenir

Colors
f04a50
ffffff
1b1b1b

Requirements
Must have
• Black back with logo included in the centre of the card.
• Our font is Avenir.

```html
<!DOCTYPE html>
<html lang="en">
<head>
<meta charset="utf-8">
<title>KBT Business Cards</title>
<link rel="stylesheet" href="https://fonts.googleapis.com/css2?family=Mulish:wght@400;600;800&display=swap">
<style>
  :root {
    --crimson: #c8194b;
    --ink: #1b1b1b;
    --paper: #ffffff;
    --stage: #d6d6d8;
    --plate-dark: #141414;
    --plate-light: #2b2b2b;
    --text-grey: #3a3a3a;
  }
  * { box-sizing: border-box; margin: 0; padding: 0; }
  html, body { width: 1200px; height: 960px; overflow: hidden; }
  body {
    background: var(--stage);
    font-family: "Mulish", "Avenir", sans-serif;
    position: relative;
  }
  .card {
    position: absolute;
    left: 280px;
    width: 640px;
    height: 391px;
    overflow: hidden;
    box-shadow: 0 10px 30px rgba(0,0,0,0.25);
  }
  /* Back */
  .card-back { top: 50px; background: var(--ink); }
  .card-back .texture {
    position: absolute; inset: 0;
    background: radial-gradient(ellipse at 40% 30%, var(--plate-light), var(--plate-dark) 75%);
  }
  .card-back .brand {
    position: absolute; left: 0; right: 0; top: 150px;
    display: flex; justify-content: center; align-items: center; gap: 16px;
  }
  .brand-square { width: 30px; height: 30px; background: var(--crimson); }
  .brand-name {
    font-weight: 800; font-size: 34px; letter-spacing: 0.5px;
    text-transform: uppercase; line-height: 1;
  }
  .card-back .brand-name { color: var(--paper); }
  .card-back .web {
    position: absolute; left: 0; right: 0; bottom: 70px;
    text-align: center; color: var(--paper);
    font-size: 16px; letter-spacing: 6px; font-weight: 600;
  }
  .card-back .web .accent { color: var(--crimson); }

  /* Front */
  .card-front { top: 500px; background: var(--paper); }
  .title-band { position: absolute; left: 0; top: 0; }
  .holder {
    position: absolute; left: 34px; top: 30px;
  }
  .holder-name {
    color: var(--crimson); font-weight: 800; font-size: 22px;
    text-transform: uppercase; letter-spacing: 0.5px;
  }
  .holder-role {
    color: var(--paper); font-size: 13px; letter-spacing: 1.5px;
    text-transform: uppercase; margin-top: 2px;
  }
  .contact {
    position: absolute; left: 34px; top: 160px;
    color: var(--text-grey); font-size: 15px; line-height: 1.55;
  }
  .contact address { font-style: normal; margin-bottom: 10px; }
  .contact-line { display: flex; align-items: center; gap: 10px; }
  .contact-line svg { width: 16px; height: 16px; flex: none; }
  .card-front .brand {
    position: absolute; left: 380px; top: 190px;
    display: flex; align-items: center; gap: 12px;
  }
  .card-front .brand-square { width: 22px; height: 22px; }
  .card-front .brand-name { color: var(--ink); font-size: 24px; }
</style>
</head>
<body>

<section class="card card-back" aria-label="Card back">
  <div class="texture" role="img" aria-label="Black tread-plate texture"></div>
  <div class="brand">
    <span class="brand-square"></span>
    <span class="brand-name">Kelbrath Baine Legal</span>
  </div>
  <p class="web">www.<span class="accent">kbtlaw</span>.co</p>
</section>

<section class="card card-front" aria-label="Card front">
  <svg class="title-band" width="640" height="180" viewBox="0 0 640 180">
    <polygon points="0,0 330,0 330,90 380,150 0,90" fill="#1b1b1b"/>
  </svg>
  <div class="holder">
    <p class="holder-name">Doran Kelbrath</p>
    <p class="holder-role">Partner</p>
  </div>
  <div class="contact">
    <address>Level 3, 118 Wendmore Street<br>Sydney NSW 2000</address>
    <p class="contact-line">
      <svg viewBox="0 0 16 16"><circle cx="8" cy="8" r="8" fill="#c8194b"/><rect x="5.5" y="3.5" width="5" height="9" rx="1" fill="none" stroke="#fff" stroke-width="1.2"/></svg>
      0461 738 524
    </p>
    <p class="contact-line">
      <svg viewBox="0 0 16 16"><rect x="1" y="3" width="14" height="10" fill="#c8194b"/><polyline points="1,3 8,9 15,3" fill="none" stroke="#fff" stroke-width="1.2"/></svg>
      doran@kbtlaw.co
    </p>
    <p class="contact-line">
      <svg viewBox="0 0 16 16"><circle cx="8" cy="8" r="7.5" fill="#c8194b"/><g fill="none" stroke="#fff" stroke-width="1"><ellipse cx="8" cy="8" rx="3" ry="6"/><line x1="2" y1="8" x2="14" y2="8"/></g></svg>
      www.kbtlaw.co
    </p>
  </div>
  <div class="brand">
    <span class="brand-square"></span>
    <span class="brand-name">Kelbrath Baine Legal</span>
  </div>
</section>

</body>
</html>
```